Brightline Balance Co Tri Page Flyer

Hi, I am after a try fold flyer to promote my new business. My Business Brightline Balance Co is a sales and service based weighing equipment business based around both scales and service. I really want to see ad ensign that grabs attention as this will be my primary drop off brochure on cold calls and mail outs as an introductory flee for my business.I want background pics of industries from Food, logistics, Medical ( as per my sample brochure states) with colours and appeal to entice customers to read not just receive and dispose!From my logo that involves green i would like to roll around that them with greys and blues.Feel free to alter my wording from my sample. i will offer some more Hi Res pics but want to get started. I think with a tri open brochure the product literature and pics can be located on each side and details through the centre page.i also feel if you can headline the wording in sections that would attract a better audience.I look forward to your exciting designs. Please let me know asap what pictures are not of a high quality so i can obtain clear Hi Res Jpegs.thanksLouis Farrugia

PLEASE ADD THE FOLLOWING PRODUCT ITEMS TO MY LIST (LISTED ON SECOND PAGE OF BBCPRODUCTS FINAL4.DOC)
AUTOMATED DRUM FILLING EQUIPMENT TO SUIT ALL APPLICATIONS ( PICS APDF 3,6,8,12)
NEW PICS ATTACHED FOR MEDICAL SCALES.
THANKS
ALSO ATTACHED MY LOGO IN A PDF TO USE
PLEASE ADD MY WEBSITE NAME, WWW.bbalanceco.com.au
Please also try to utilise the green Tick correct symbol in my logo in the flyer as a symbol of CORRECT.
Thankyou
MARTIN

Target Market(s)

Food manufacturing, medical, logistics, Industrial, retail Applications

Industry/Entity Type

Business

Colors
919191
9d9d9d
00a990
33a6d7

Requirements
Must have
• Appeal for potential customers to read!
• Wording to appeal to readers
Nice to have
• Colours to match my logo, greens, greys, blues
• Background images of manufacturing Industires.
• I would like to emphasise in 1 line that high quality customer service is what I am about, not calling a number put on hold put through to a department that does not answer leaving messages etc etc you are not a number with me!!

```html
<!DOCTYPE html>
<html lang="en">
<head>
<meta charset="utf-8">
<title>Brightline Balance Co – Products</title>
<link href="https://fonts.googleapis.com/css2?family=Roboto+Condensed:wght@400;700&display=swap" rel="stylesheet">
<style>
:root{
  --page:#ffffff;
  --blue-light:#7fd3f0;
  --blue:#1e8fd0;
  --blue-deep:#1170b8;
  --green-bright:#3cb54a;
  --orange:#f7941d;
  --white:#ffffff;
}
*{box-sizing:border-box;margin:0;padding:0}
html,body{width:859px;height:1200px;overflow:hidden;background:var(--page)}
body{font-family:"Roboto Condensed",Arial,sans-serif;position:relative}
.panel{
  position:absolute;left:110px;top:40px;width:712px;height:1125px;
  background:linear-gradient(180deg,var(--blue-light) 0%,var(--blue) 55%,var(--blue-deep) 100%);
}
.photo{
  position:absolute;border:4px solid var(--green-bright);background:linear-gradient(160deg,#f4f4f4,#bdbdbd);
}
.photo.dark{background:linear-gradient(160deg,#7a7a7a,#2f2f2f)}
.photo.warm{background:linear-gradient(160deg,#f2c14e,#e07a1f)}
.photo.cool{background:linear-gradient(160deg,#e8eef2,#9aa7b0)}
.products{
  position:absolute;left:362px;top:118px;width:440px;color:var(--white);
}
.products h1{font-size:32px;font-weight:700;letter-spacing:1px;margin-bottom:16px}
.products ul{list-style:none}
.products li{
  position:relative;padding-left:28px;font-size:19px;font-weight:400;line-height:1.3;margin-bottom:8px;
  text-align:justify;hyphens:auto;
}
.products li svg{position:absolute;left:0;top:4px;width:17px;height:17px}
.cta{
  position:absolute;left:100px;top:915px;width:690px;height:95px;background:var(--orange);
  color:var(--white);font-size:33px;font-weight:700;text-align:center;line-height:1.2;
  display:flex;align-items:center;justify-content:center;padding:0 40px;
}
.services{
  position:absolute;left:125px;top:1035px;display:grid;grid-template-columns:repeat(3,auto);
  column-gap:24px;row-gap:16px;color:var(--white);font-size:18px;
}
.services span{display:flex;align-items:center;gap:8px}
.services svg{width:17px;height:17px}
.contact{
  position:absolute;left:490px;top:1033px;color:var(--white);font-size:17px;line-height:2.1;
}
</style>
</head>
<body>
<svg width="0" height="0" style="position:absolute">
  <symbol id="tick" viewBox="0 0 18 18">
    <rect x="1" y="1" width="16" height="16" fill="#ffffff" stroke="#1170b8" stroke-width="1"/>
    <path d="M4 9.5l3.2 3.2L14 5" fill="none" stroke="#1170b8" stroke-width="2.4"/>
  </symbol>
</svg>

<div class="panel"></div>

<div class="photo" style="left:80px;top:60px;width:150px;height:140px" role="img" aria-label="Digital counting scale"></div>
<div class="photo" style="left:228px;top:95px;width:100px;height:385px" role="img" aria-label="Medical height and weight scale"></div>
<div class="photo cool" style="left:80px;top:210px;width:145px;height:200px" role="img" aria-label="Linear weigher filling machine"></div>
<div class="photo" style="left:80px;top:420px;width:145px;height:160px" role="img" aria-label="Platform bench scale"></div>
<div class="photo warm" style="left:228px;top:490px;width:100px;height:205px" role="img" aria-label="Pallet jack scale"></div>
<div class="photo" style="left:80px;top:590px;width:145px;height:150px" role="img" aria-label="Bench scale with indicator"></div>
<div class="photo dark" style="left:228px;top:705px;width:100px;height:100px" role="img" aria-label="Receipt label printer"></div>
<div class="photo cool" style="left:80px;top:750px;width:145px;height:110px" role="img" aria-label="Scales on display"></div>
<div class="photo dark" style="left:80px;top:870px;width:120px;height:40px" role="img" aria-label="Floor scale beams"></div>

<section class="products">
  <h1>PRODUCTS</h1>
  <ul>
    <li><svg><use href="#tick"/></svg>Electronic Platform Scales Ranging From 30kg-600kg</li>
    <li><svg><use href="#tick"/></svg>Printers and Labellers to suit your requirements</li>
    <li><svg><use href="#tick"/></svg>Linear Weighers to suit all Applications</li>
    <li><svg><use href="#tick"/></svg>Electronic Floor Scales Ranging From 1000kg - 3000kg(Trade Approved)</li>
    <li><svg><use href="#tick"/></svg>Full Range of Electronic and Mechanical Hanging and Crane Scales Ranging from10kg -10Tonne</li>
    <li><svg><use href="#tick"/></svg>Vet Scales ranging from 20kg-300kg</li>
    <li><svg><use href="#tick"/></svg>Electronic Baby Scales</li>
    <li><svg><use href="#tick"/></svg>Pallet Jack Scales to 2000kg</li>
    <li><svg><use href="#tick"/></svg>Full range of TRADE APPROVED SCALES</li>
    <li><svg><use href="#tick"/></svg>Coin and Note Counting Scales</li>
    <li><svg><use href="#tick"/></svg>Shipping/Parcel Scales to suit any application</li>
    <li><svg><use href="#tick"/></svg>High Precision Electronic Balances Ranging From 100-8000g</li>
    <li><svg><use href="#tick"/></svg>Full Range of Electronic Weighing Indicators To suit any application</li>
    <li><svg><use href="#tick"/></svg>Full range of Load Cells and Fittings to suit any Application</li>
    <li><svg><use href="#tick"/></svg>REPAIRS ON ALL WEIGHING AND PACKAGING EQUIPMENT ALL MAKES AND MODELS</li>
  </ul>
</section>

<div class="cta">ASK ABOUT OUR RANGE OF PACKAGING AND FILLING EQUIPMENT</div>

<div class="services">
  <span><svg><use href="#tick"/></svg>Weighing</span>
  <span><svg><use href="#tick"/></svg>Packaging</span>
  <span><svg><use href="#tick"/></svg>Testing</span>
  <span><svg><use href="#tick"/></svg>Sales</span>
  <span><svg><use href="#tick"/></svg>Services</span>
  <span><svg><use href="#tick"/></svg>Hire</span>
</div>

<div class="contact">
  <p>Contact Martin: 0400 123 456</p>
  <p>Email: martin@bbalanceco.com.au</p>
</div>
</body>
</html>
```